Counseling Practice Business Card

I need a professional looking business card incorporating my new logo that was just completed. Card needs to incorporate my name and title, description of my specialty, my address, my phone number, my fax number, my email and my website URL. I need to be able to choose design on/with different paper colors and textures.
I do not have a lot of business card ideas so I am open to anything but I want bold,sharp, clear card without additional designs other than my logo (see attached file info). I am open to different color backgrounds or paper colors including black. I do not like traditional brackets around area codes in phone number or dashes between numbers in phone number. Am open to other ways of presenting including periods between numbers as appropriate. I do not know enough to know what I like yet but I want card to coordinate and work together with my logo. My practice emphasizes natural mental health interventions so any use of color (with background paper color or the blue and green in my logo) that elicits nature is nice. In addition to black, any natural brown or wood looking background might be desirable also. Most of the offerings so far look very similar and boring.

Target Market(s)

Potential therapy clients and other professionals

Contact Information for Business Card

Card information:
Gerald M. Whitcombe, Ph.D.
Licensed Clinical Psychologist
Integrative Health Coach
4812 Marlowe Ridge Blvd SE
Suite 310
Duluth, GA 30096
(770) 415-2983 phone
(770) 581-4096 fax
drgeraldwhitcombe@quillmarsh.net
brightfernwellness.net

Font styles to use
Serif
Sans Serif
Other font styles liked:
• anything that you think looks crisp, clear and easily readable

Requirements
Must have
• Any color used should coordinate with my logo design (see attached files).
• Card should be printed horizontally so top and bottom are longest sides of rectangle.
• Background color or paper color should complement and highlight logo. Do not like a white background. black, grey, brown or any color my logo would blend well with.
Nice to have
• I would like designer to utilize color to highlight letters/name or phone-fax-web symbols.
• Bottom edge of card could be highlighted if appropriate to an idea.
Should not have
• I would NOT want the card to have a pure white background at all.
• No clear cards.
• Cards should be oriented with long sides on bottom and top, NOT sides. DO NOT LIKE THIS THIN TALL ORIENTATION.

```html
<!DOCTYPE html>
<html lang="en">
<head>
<meta charset="utf-8">
<title>Brightfern Wellness – Business Card</title>
<link href="https://fonts.googleapis.com/css2?family=PT+Sans:wght@400;700&display=swap" rel="stylesheet">
<style>
  :root {
    --backdrop: #4a403a;
    --card: #1b1c1e;
    --brand-blue: #2e6fb3;
    --brand-green: #1f8a4c;
    --text-light: #cfcfcf;
    --rule: #6a6a6a;
  }
  * { margin: 0; padding: 0; box-sizing: border-box; }
  html, body {
    width: 1200px; height: 864px; overflow: hidden;
    background: var(--backdrop);
    font-family: "PT Sans", Arial, sans-serif;
  }
  .sheet {
    width: 1200px; height: 864px;
    display: flex; align-items: center; justify-content: center; gap: 40px;
  }
  .card {
    position: relative;
    width: 540px; height: 309px;
    background: var(--card);
    border-radius: 3px;
    box-shadow: 0 6px 18px rgba(0,0,0,.45);
    color: var(--text-light);
  }
  /* Front */
  .card-front {
    display: flex; flex-direction: column; align-items: center; justify-content: center; gap: 26px;
  }
  .wordmark {
    font-weight: 700; color: var(--brand-blue);
    display: flex; align-items: center; gap: 10px;
  }
  .wordmark-dot {
    width: 14px; height: 14px; border-radius: 50%; background: var(--brand-green);
  }
  .card-front .wordmark { font-size: 40px; }
  .front-url {
    font-size: 14px; letter-spacing: 4px; color: var(--text-light);
  }
  /* Back */
  .card-back .identity {
    position: absolute; left: 30px; top: 34px;
  }
  .holder-name {
    font-size: 17px; font-weight: 700; color: var(--brand-blue);
    text-transform: uppercase; letter-spacing: .3px;
  }
  .holder-title {
    font-size: 14px; color: var(--brand-green); line-height: 1.3;
  }
  .card-back .wordmark {
    position: absolute; right: 28px; top: 40px; font-size: 22px;
  }
  .card-back .wordmark-dot { width: 9px; height: 9px; }
  .divider {
    position: absolute; left: 30px; right: 28px; top: 112px;
    height: 1px; background: var(--rule);
  }
  .contact-list {
    position: absolute; left: 30px; top: 126px;
    list-style: none; font-size: 13.5px; line-height: 1.55;
  }
  .contact-list li { display: flex; align-items: center; gap: 8px; }
  .contact-icon { width: 12px; height: 12px; fill: var(--brand-blue); flex: none; }
  .address-rule {
    position: absolute; left: 30px; right: 28px; top: 214px;
    height: 1px; background: var(--rule);
  }
  .address {
    position: absolute; right: 28px; top: 226px;
    font-style: normal; text-align: right; font-size: 14px; line-height: 1.4;
  }
</style>
</head>
<body>
<main class="sheet">
  <section class="card card-front" aria-label="Card front">
    <div class="wordmark"><span class="wordmark-dot"></span>Brightfern Wellness</div>
    <p class="front-url">www.brightfernwellness.net</p>
  </section>

  <section class="card card-back" aria-label="Card back">
    <div class="identity">
      <h1 class="holder-name">Gerald M. Whitcombe, Ph.D.</h1>
      <p class="holder-title">Licensed Clinical Psychologist</p>
      <p class="holder-title">Integrative Health Coach</p>
    </div>
    <div class="wordmark"><span class="wordmark-dot"></span>Brightfern Wellness</div>
    <div class="divider"></div>
    <ul class="contact-list">
      <li>
        <svg class="contact-icon" viewBox="0 0 12 12" aria-hidden="true"><path d="M2.5 0.8l2 0.1 0.9 2.6-1.3 1a7 7 0 0 0 2.9 2.9l1-1.3 2.6.9.1 2a1.2 1.2 0 0 1-1.3 1.2A10 10 0 0 1 1.3 2.1 1.2 1.2 0 0 1 2.5.8z"/></svg>
        (770) 415-2983
      </li>
      <li>
        <svg class="contact-icon" viewBox="0 0 12 12" aria-hidden="true"><path d="M3 0h5v3H3zM1 4h10v6H9v2H3v-2H1zM4 8v3h4V8z"/></svg>
        (770) 581-4096
      </li>
      <li>
        <svg class="contact-icon" viewBox="0 0 12 12" aria-hidden="true"><path d="M0 2h12v1L6 7 0 3zM0 4.3l6 4 6-4V10H0z"/></svg>
        drgeraldwhitcombe@quillmarsh.net
      </li>
      <li>
        <svg class="contact-icon" viewBox="0 0 12 12" aria-hidden="true"><circle cx="6" cy="6" r="6"/></svg>
        www.brightfernwellness.net
      </li>
    </ul>
    <div class="address-rule"></div>
    <address class="address">
      4812 Marlowe Ridge Blvd SE<br>
      Suite 310<br>
      Duluth, GA 30096
    </address>
  </section>
</main>
</body>
</html>
```